Calder Vossik - Cinematographer

NEED:
I'm looking for a sleek, professional, modern business card that will give give the recipient the impression that they can trust their production will go smoothly by hiring me. I will bring creativity and knowledge to their shoot, so that we can create powerful images.
I am looking for a card with a strong style and design ethos that could be expanded to a website and a full visual/graphic/design entity for me.
ABOUT ME:
I am a mid-twenties cinematographer, I work on music video, narrative short, commercial, and corporate projects. I blend the science and artistry of cameras and filmmaking to tell a story. I'm an artist, a technician, and a manager.
DESIGN:
I like sleek, simple design. Black, dark grays, white, dark navy, steel blues, I love cyan, but also cyan and red. I am not a fan of earthy tones. I generally prefer modern, san-serif fonts over serifs. My old logo was based on an aperture, a multi-blade device at the back of a lens that controls how much light passes through, but I made it with so many colors, that it doesn't necessarily lend itself to a specific color-scheme or design ethos. I liked that the aperture design provided a sense of the technical requirements of my job. I'm a fan of matte business cards, but am open to plenty of specialty print processes to make an outstanding card.
ATTACHED FILES:
My Old Rainbox Aperture Logo, plus a few designs I've tried playing around with, but am not tied to. I AM OPEN TO NEW DESIGNS, DO NOT FEEL TIED TO THIS.
**I've pulled my old logo down from the attached files, and instead attached other business cards I like, so as not to mislead you where I would like to go.
INFO:
Name: Calder Vossik
Job: Cinematographer
Email: ccvossik@lumenpost.net
Phone: 415.555.0193
Website: caldervossik.com
Updates
I'm adding some images of other cards that I like, and removing my old logo, since I'm looking for something new, and don't want that old logo to push anyone a certain direction.

```html
<!DOCTYPE html>
<html lang="en">
<head>
<meta charset="utf-8">
<title>Calder Vossik – Cinematographer business card</title>
<link rel="stylesheet" href="https://fonts.googleapis.com/css2?family=Quicksand:wght@500;600;700&display=swap">
<style>
  :root {
    --backdrop: #dcdcde;
    --card-dark: #47474a;
    --card-darker: #2b2b2d;
    --teal-deep: #3b8c8b;
    --cyan: #47c6c9;
    --ink: #161617;
    --white: #ffffff;
    --glow: #f2f2f2;
  }
  html, body {
    margin: 0;
    width: 1200px;
    height: 900px;
    overflow: hidden;
    background: var(--backdrop);
  }
  .stage {
    position: relative;
    width: 1200px;
    height: 900px;
  }
  .card {
    position: absolute;
    width: 560px;
    height: 320px;
    border-radius: 28px;
    overflow: hidden;
    box-shadow: 0 10px 28px rgba(0,0,0,0.25);
  }
  .card svg { display: block; }
  .card-front { left: 90px; top: 90px; }
  .card-back { left: 550px; top: 490px; }
  .brand-name,
  .holder-name,
  .holder-role,
  .contact-text {
    font-family: "Quicksand", sans-serif;
    fill: var(--white);
  }
  .brand-name { font-weight: 700; font-size: 52px; }
  .holder-name { font-weight: 600; font-size: 34px; }
  .holder-role { font-weight: 600; font-size: 25px; }
  .contact-text { font-weight: 500; font-size: 18px; }
  .contact-icon { fill: var(--white); stroke: none; }
  .contact-icon-line { fill: none; stroke: var(--card-dark); stroke-width: 1.4; }
</style>
</head>
<body>
<main class="stage">

  <section class="card card-front" aria-label="Card front">
    <svg width="560" height="320" viewBox="0 0 560 320">
      <defs>
        <radialGradient id="front-glow" cx="0.6" cy="0.45" r="0.6">
          <stop offset="0" stop-color="var(--glow)"/>
          <stop offset="0.35" stop-color="#8a8a8c"/>
          <stop offset="1" stop-color="var(--card-dark)"/>
        </radialGradient>
      </defs>
      <rect class="front-base" width="560" height="320" fill="url(#front-glow)"/>
      <circle class="brand-mark" cx="440" cy="112" r="66" fill="var(--card-darker)"/>
      <text class="brand-name" x="48" y="262">Calder Vossik</text>
    </svg>
  </section>

  <section class="card card-back" aria-label="Card back">
    <svg width="560" height="320" viewBox="0 0 560 320">
      <rect class="back-base" width="560" height="320" fill="var(--card-dark)"/>
      <path class="band-left" d="M0 0 H95 C70 120 90 250 180 320 H0 Z" fill="var(--teal-deep)"/>
      <path class="swoosh-right" d="M95 0 H560 V250 C460 110 250 30 95 0 Z" fill="var(--cyan)"/>
      <path class="swoosh-edge" d="M95 0 C250 30 460 110 560 250" fill="none" stroke="var(--ink)" stroke-width="3"/>
      <path class="band-edge" d="M95 0 C70 120 90 250 180 320" fill="none" stroke="var(--ink)" stroke-width="3"/>

      <text class="holder-name" x="150" y="140">Calder Vossik</text>
      <text class="holder-role" x="166" y="172">Cinematographer</text>

      <g class="contact-phone">
        <path class="contact-icon" d="M300 229 c2-2 4-2 5 0 l3 3 c1 2 0 3-1 4 l-1 1 c1 3 3 5 6 6 l1-1 c1-1 3-2 4-1 l3 3 c2 1 2 3 0 5 l-2 2 c-7 3-21-11-18-20 z"/>
        <text class="contact-text" x="330" y="246">415.555.0193</text>
      </g>
      <g class="contact-email">
        <rect class="contact-icon" x="299" y="260" width="23" height="16" rx="2"/>
        <path class="contact-icon-line" d="M300 261 L310.5 270 L321 261"/>
        <text class="contact-text" x="330" y="275">ccvossik@lumenpost.net</text>
      </g>
      <g class="contact-web">
        <circle class="contact-icon" cx="310.5" cy="297" r="10"/>
        <path class="contact-icon-line" d="M300.5 297 H320.5 M310.5 287 V307 M302.5 292 H318.5 M302.5 302 H318.5 M310.5 287 C303.5 292 303.5 302 310.5 307 M310.5 287 C317.5 292 317.5 302 310.5 307"/>
        <text class="contact-text" x="330" y="304">www.caldervossik.com</text>
      </g>
    </svg>
  </section>

</main>
</body>
</html>
```